Marwick Law Letterhead

We need a new letterhead design for a Law Firm. The address for the law firm is 1475 Calloway Street, Suite 210, Houston, Texas 77041. Phone Number: 832-361-9027; Fax Number: 832-614-7359. The logo is uploaded to the project.

```html
<!DOCTYPE html>
<html lang="en">
<head>
<meta charset="utf-8">
<title>Marwick Law Letterhead</title>
<link rel="stylesheet" href="https://fonts.googleapis.com/css2?family=Cinzel:wght@400;500&family=Montserrat:wght@400&display=swap">
<style>
  :root {
    --backdrop: #e4e4e4;
    --paper: #ffffff;
    --navy: #1f2f66;
    --crimson: #c8202c;
    --ink: #1a1a1a;
  }
  * { margin: 0; padding: 0; box-sizing: border-box; }
  html, body {
    width: 1200px;
    height: 960px;
    overflow: hidden;
    background: var(--backdrop);
  }
  .letterhead {
    position: absolute;
    left: 252px;
    top: 30px;
    width: 696px;
    height: 900px;
    background: var(--paper);
    box-shadow: 0 4px 18px rgba(0,0,0,0.12);
    overflow: hidden;
  }
  .brand {
    position: absolute;
    left: 54px;
    top: 54px;
    display: flex;
    align-items: center;
    gap: 12px;
  }
  .brand-dot {
    width: 40px;
    height: 40px;
    border-radius: 50%;
    background: var(--navy);
    flex-shrink: 0;
  }
  .brand-text { display: flex; flex-direction: column; }
  .brand-name {
    font-family: "Cinzel", serif;
    font-weight: 500;
    font-size: 28px;
    color: var(--navy);
    letter-spacing: 1px;
    line-height: 1.1;
    white-space: nowrap;
  }
  .brand-rule {
    border-top: 1px solid var(--crimson);
    margin: 5px 0 4px;
  }
  .brand-tagline {
    font-family: "Cinzel", serif;
    font-weight: 500;
    font-size: 7.5px;
    letter-spacing: 1.6px;
    color: var(--crimson);
    white-space: nowrap;
  }
  .contact {
    position: absolute;
    right: 50px;
    bottom: 56px;
    font-family: "Montserrat", sans-serif;
    color: var(--ink);
  }
  .contact-phones {
    display: flex;
    gap: 16px;
    font-size: 12px;
    margin-bottom: 6px;
  }
  .contact-item { display: flex; align-items: center; gap: 6px; white-space: nowrap; }
  .contact-item svg { width: 12px; height: 12px; fill: var(--crimson); }
  .contact-address { font-size: 12px; white-space: nowrap; }
  .contact-rule {
    border-top: 1px solid var(--crimson);
    margin-top: 8px;
  }
</style>
</head>
<body>
  <main class="letterhead">
    <header class="brand">
      <span class="brand-dot" aria-hidden="true"></span>
      <div class="brand-text">
        <span class="brand-name">Marwick Law</span>
        <span class="brand-rule"></span>
        <span class="brand-tagline">STEADY COUNSEL FOR EVERY HARD ROAD</span>
      </div>
    </header>

    <footer class="contact">
      <div class="contact-phones">
        <span class="contact-item">
          <svg viewBox="0 0 24 24" aria-label="Phone"><path d="M6.6 10.8a15.1 15.1 0 0 0 6.6 6.6l2.2-2.2c.3-.3.7-.4 1-.2 1.1.4 2.3.6 3.6.6.6 0 1 .4 1 1V20c0 .6-.4 1-1 1A17 17 0 0 1 3 4c0-.6.4-1 1-1h3.5c.6 0 1 .4 1 1 0 1.3.2 2.5.6 3.6.1.3 0 .7-.2 1z"/></svg>
          832-361-9027
        </span>
        <span class="contact-item">
          <svg viewBox="0 0 24 24" aria-label="Fax"><path d="M6 2h10l2 2v5H6zM4 10h16a2 2 0 0 1 2 2v6h-4v4H6v-4H2v-6a2 2 0 0 1 2-2zm4 6v4h8v-4z"/></svg>
          832-614-7359
        </span>
      </div>
      <div class="contact-address">1475 Calloway Street, Suite 210, Houston, Texas 77041</div>
      <div class="contact-rule"></div>
    </footer>
  </main>
</body>
</html>
```